Property Services Company Needs a Brochure Design

Looking for a new brochure design for an existing property services company.

We provide a range of property services from, market research, real estate brokerage, valuation and appraisal, property development and other real estate consulting services.

We would like a fresh modern brochure design with good graphics and features. Our colours are white, blue and orange.

The design should communicate, attention to detail, superior service delivery and distinction in results.
Updates

I would like the brochure to be roughly about 20 pages.

Containing the following,

1) An introduction
2) Contents Page
2) What we do
3) Our Services
4) Agency & Brokerage
5) Real Estate Consulting
6) Market Research
7) Appraisal & Valuation
8) Project Management
9) Property Development

I would also like icons to represent items 4,5,6,7,8 & 9, they should be represented vertically on each of the pages from the contents page and highlighted individually on the pages that they represent.. i.e. on appraisal & valuation page, all six icons will be arranged vertically and the appraisal and valuations icon will be highlighted.

I will also like to have images that depict the services on the various pages.

I have some pages I think will flow which I will upload shortly.

Industry/Entity Type

Real Estate

Font styles to use
Serif

Colors
f78f20
0455a3

```html
<!DOCTYPE html>
<html lang="en">
<head>
<meta charset="utf-8">
<title>Halvern Property Services – Brochure Cover Spread</title>
<link href="https://fonts.googleapis.com/css2?family=Tinos:wght@400&family=Open+Sans:wght@400&family=Arimo:wght@400&display=swap" rel="stylesheet">
<style>
  :root {
    --orange: #e3600f;
    --navy: #2a2160;
    --white: #ffffff;
    --ink: #111111;
    --logo-ink: #3a3a3c;
    --frame: #8a8a8a;
    --photo-light: #e9e2d3;
    --photo-mid: #b9a78a;
    --photo-dark: #5f5240;
  }
  * { margin: 0; padding: 0; box-sizing: border-box; }
  html, body { width: 1200px; height: 864px; overflow: hidden; background: var(--white); }
  .canvas {
    position: relative; width: 1200px; height: 864px;
    border: 1px solid var(--frame); background: var(--white);
  }
  .spread {
    position: absolute; left: 40px; top: 35px; width: 1120px; height: 794px;
    border: 1px solid var(--frame); background: var(--white);
  }
  .page { position: absolute; top: 0; height: 100%; }
  .page--back { left: 0; width: 560px; border-right: 1px solid var(--frame); }
  .page--front { left: 560px; width: 560px; }

  .intro-block { position: absolute; left: 0; top: 0; width: 560px; height: 357px; }
  .intro-block__orange { position: absolute; left: 0; top: 0; width: 285px; height: 100%; background: var(--orange); }
  .intro-block__navy { position: absolute; left: 285px; top: 0; width: 275px; height: 100%; background: var(--navy); }
  .intro-text {
    position: absolute; left: 56px; top: 73px; width: 460px;
    font-family: "Tinos", "Times New Roman", serif; color: var(--white);
    font-size: 12.4px; line-height: 15.6px;
  }
  .intro-text h2 { font-weight: 400; font-size: 15px; letter-spacing: 0.3px; margin-bottom: 4px; }
  .intro-text p { margin-bottom: 5px; }

  .brand { position: absolute; display: flex; align-items: center; gap: 10px; }
  .brand__mark { width: 22px; height: 22px; background: var(--navy); }
  .brand__words { font-family: "Open Sans", Arial, sans-serif; color: var(--logo-ink); }
  .brand__name { display: block; font-size: 36px; line-height: 38px; }
  .brand__tag { display: block; font-size: 13px; line-height: 15px; text-align: right; }
  .brand--back { left: 174px; top: 614px; }
  .brand--back .brand__name { font-size: 34px; }
  .brand--front { left: 300px; top: 55px; }

  .contact {
    position: absolute; left: 110px; top: 676px; width: 320px; text-align: center;
    font-family: "Arimo", Arial, sans-serif; font-size: 12px; line-height: 13.6px; color: var(--ink);
  }
  .contact svg { width: 11px; height: 11px; vertical-align: -1px; margin-right: 2px; }

  .band { position: absolute; left: 0; width: 100%; }
  .band--orange { background: var(--orange); }
  .band--navy { background: var(--navy); }

  .photo {
    position: absolute; left: 0; top: 189px; width: 560px; height: 483px;
    background:
      linear-gradient(180deg, var(--photo-light) 0%, var(--photo-mid) 45%, var(--photo-dark) 62%, var(--photo-mid) 80%, var(--photo-light) 100%);
  }
</style>
</head>
<body>
<div class="canvas">
  <div class="spread">

    <section class="page page--back">
      <div class="intro-block">
        <div class="intro-block__orange"></div>
        <div class="intro-block__navy"></div>
        <div class="intro-text">
          <h2>INTRODUCTION</h2>
          <p>HALVERN was incorporated in 1984 as an interior design and property development company. Over the years we have expanded our service with a foundation based on core strengths, unrivalled local expertise, network and knowledge combined with strategic partnerships.</p>
          <p>Halvern offers a comprehensive range of services on a local, regional, national and international basis to tenants, owners, and investors within the residential and commercial property market.</p>
          <p>Our clients depend on our ability to draw on</p>
          <p>Our clients depend on our ability to draw on years of experience in the local market, our professionals know their communities and the property market inside and out, and provide knowledgeable, creative solutions to all their real estate needs.</p>
          <p>We currently provide services to corporations, financial institutions, government agencies, public sector entities, developers and investors. Our knowledge, expertise, experience and technological resources allow us to be a superior service provider.</p>
        </div>
      </div>

      <div class="brand brand--back">
        <span class="brand__mark"></span>
        <span class="brand__words">
          <span class="brand__name">Halvern</span>
          <span class="brand__tag">Property Services</span>
        </span>
      </div>

      <address class="contact" style="font-style:normal">
        <div><svg viewBox="0 0 12 12"><path d="M6 0a4 4 0 0 0-4 4c0 3 4 8 4 8s4-5 4-8a4 4 0 0 0-4-4zm0 5.6a1.6 1.6 0 1 1 0-3.2 1.6 1.6 0 0 1 0 3.2z" fill="#e3600f"/></svg>12th floor, MARLOW HOUSE, 88, Harbour Road</div>
        <div>Lagos, Nigeria</div>
        <div><svg viewBox="0 0 12 12"><path d="M3 1 1.5 2.5C1 6 6 11 9.5 10.5L11 9 8.6 7.2 7.4 8.2C5.8 7.4 4.6 6.2 3.8 4.6L4.8 3.4z" fill="#e3600f"/></svg>+234 1 5550142 &nbsp;<svg viewBox="0 0 12 12"><rect x="1" y="5" width="10" height="5" rx="1" fill="#e3600f"/><rect x="3" y="1" width="6" height="4" fill="#e3600f"/></svg>+234 1 5550178</div>
        <div><svg viewBox="0 0 12 12"><rect x="0.5" y="2" width="11" height="8" fill="#2a2160"/><path d="M0.5 2 6 7l5.5-5" stroke="#fff" fill="none"/></svg>info@halvern.example &nbsp;<svg viewBox="0 0 12 12"><circle cx="6" cy="6" r="5.3" fill="#2a2160"/><path d="M0.7 6h10.6M6 0.7v10.6M6 0.7c-3 3-3 7.6 0 10.6M6 0.7c3 3 3 7.6 0 10.6" stroke="#fff" stroke-width="0.7" fill="none"/></svg>www.halvern.example</div>
      </address>

      <div class="band band--orange" style="top:745px;height:14px"></div>
      <div class="band band--navy" style="top:765px;height:29px"></div>
    </section>

    <section class="page page--front">
      <div class="brand brand--front">
        <span class="brand__mark"></span>
        <span class="brand__words">
          <span class="brand__name">Halvern</span>
          <span class="brand__tag">Property Services</span>
        </span>
      </div>

      <div class="band band--orange" style="top:133px;height:13px"></div>
      <div class="band band--orange" style="top:155px;height:12px"></div>
      <div class="band band--orange" style="top:175px;height:14px"></div>

      <div class="photo" role="img" aria-label="Photograph of a bright modern office lobby with polished floor, columns and reception desk"></div>

      <div class="band band--navy" style="top:674px;height:12px"></div>
      <div class="band band--navy" style="top:696px;height:12px"></div>
      <div class="band band--navy" style="top:717px;height:13px"></div>
    </section>

  </div>
</div>
</body>
</html>
```